Oil and Gas Exploration and Production company needs a business card design

We need a business card design using our logo and colors in the logo. We want a mainstream design.

```html
<!DOCTYPE html>
<html lang="es">
<head>
<meta charset="utf-8">
<title>Talma Oil &amp; Gas – Business Card</title>
<link rel="stylesheet" href="https://fonts.googleapis.com/css2?family=EB+Garamond:wght@400;600;700&display=swap">
<style>
  :root {
    --page-bg: #d8d8d5;
    --card-bg: #efefed;
    --gold: #b47a1c;
    --gold-dark: #8a5a12;
    --ink: #1d1b18;
    --text: #4a4540;
  }
  * { margin: 0; padding: 0; box-sizing: border-box; }
  html, body { width: 1200px; height: 970px; overflow: hidden; }
  body {
    background: var(--page-bg);
    font-family: "EB Garamond", Georgia, serif;
    position: relative;
  }
  .business-card {
    position: absolute;
    left: 100px; top: 190px;
    width: 1000px; height: 590px;
    background: var(--card-bg);
    box-shadow: 0 10px 30px rgba(0,0,0,0.18);
  }
  .brand {
    position: absolute;
    left: 315px; top: 120px;
    display: flex; align-items: center; gap: 16px;
  }
  .brand-dot {
    width: 46px; height: 46px; border-radius: 50%;
    background: var(--ink);
  }
  .brand-name {
    font-size: 64px; font-weight: 700; color: var(--ink);
    line-height: 1; letter-spacing: 0.5px;
  }
  .divider {
    position: absolute;
    left: 55px; top: 402px;
    width: 686px; height: 3px;
    background: var(--gold-dark);
  }
  .holder {
    position: absolute;
    right: 73px; top: 362px;
    text-align: right;
  }
  .holder-name {
    font-size: 23px; font-weight: 600; color: var(--gold-dark); line-height: 1.2;
  }
  .holder-title {
    font-size: 19px; color: var(--ink); line-height: 1.3;
  }
  .contacts {
    position: absolute;
    left: 55px; top: 428px;
    list-style: none;
  }
  .contact-item {
    display: flex; align-items: center; gap: 18px;
    height: 40px;
    font-size: 19px; color: var(--text);
  }
  .contact-icon { width: 20px; height: 20px; fill: var(--gold-dark); flex: none; }
  .address {
    position: absolute;
    right: 73px; top: 478px;
    text-align: right;
    font-style: normal;
    font-size: 19px; font-weight: 600; color: var(--gold-dark);
    line-height: 1.5;
  }
  .bottom-band {
    position: absolute;
    left: 0; bottom: 0;
    width: 100%; height: 12px;
    background: linear-gradient(90deg, var(--gold-dark), var(--gold), var(--gold-dark));
  }
</style>
</head>
<body>
  <div class="business-card">
    <div class="brand">
      <span class="brand-dot"></span>
      <span class="brand-name">Talma Oil &amp; Gas</span>
    </div>

    <div class="holder">
      <p class="holder-name">Marisol Ortega</p>
      <p class="holder-title">Chief Executive Offer</p>
    </div>

    <div class="divider"></div>

    <ul class="contacts">
      <li class="contact-item">
        <svg class="contact-icon" viewBox="0 0 24 24" aria-hidden="true"><path d="M3 9c0-3 4-5 9-5s9 2 9 5v2h-5V9c-1-.6-2.4-1-4-1s-3 .4-4 1v2H3zM6 12h12l2 8H4z"/></svg>
        <span>+34 900 418 235</span>
      </li>
      <li class="contact-item">
        <svg class="contact-icon" viewBox="0 0 24 24" aria-hidden="true"><path d="M2 5h20v14H2z" /><path d="M3 6l9 7 9-7" fill="none" stroke="#efefed" stroke-width="2"/></svg>
        <span>info@talmaoil.example</span>
      </li>
      <li class="contact-item">
        <svg class="contact-icon" viewBox="0 0 24 24" aria-hidden="true"><circle cx="12" cy="12" r="9"/></svg>
        <span>@talmaoil</span>
      </li>
    </ul>

    <address class="address">
      Calle del Prado 14<br>
      Oficina 2B, 28014, Madrid
    </address>

    <div class="bottom-band"></div>
  </div>
</body>
</html>
```